Business Cards for IT Consulting Company (Managed Service Provider)

I am looking to have some business cards printed and would like some designs. We are an IT Consulting company based in Vancouver BC. I would like a nice clean and modern look to the cards. I have uploaded all the versions of my logo so parts can be used as needed. Here is a snippit from our website homepage:

Quillbrook Networks Ltd. is an IT Solutions Partner located in Vancouver BC, Canada. We offer IT solutions and support to customers in the greater Vancouver Area. With expertise in Microsoft platforms, as well as Linux and Mac OSX and over 12 years experience in the IT industry, Quillbrook Networks is dedicated to offering our clients top quality service and products. We take pride in the solutions we offer our customers. The greatest compliment a client can give us is to recommend our services.

Quillbrook Networks Ltd. offers a wide range of IT services from onsite service to remote support and managed service solutions. This allows clients to choose the support path that best suits their company’s needs. Supporting many different sized companies from small to enterprise level over the past 12 years Quillbrook Networks has the experience and expertise needed to ensure things run smoothly. Allowing our clients to focus on doing business.

Revolutionizing the way IT services are delivered.

Quillbrook Networks is dedicated to providing our clients with IT solutions that work and grow with them for years to come. This philosophy helps save money in the long run instead of replacing equipment constantly. Far too often IT solutions are not well thought out and while possibly solving the problem at hand, require replacement due to growth or quality within a very short time frame. Quillbrook Networks takes pride in providing solutions that will last and be able to accommodate growth without the need for replacement.

Industry/Entity Type

Information Technology

Contact Information for Business Card

Quillbrook Networks Ltd.
(Employee Name)
Eml: (Employees Email Address)
Web: quillbrook.me
Ph: 604-555-0148

Font styles to use
Serif
Sans Serif

Requirements
Must have
• The Company logo and company colors.
Nice to have
• - Our tag line: "Revolutionizing IT Services" or "Revolutionizing the way IT services are delivered."
• - Also I really like the idea of nature and technology together blending which is sort of where my logo came from so integrating that somehow onto the business cards would be great.

```html
<!DOCTYPE html>
<html lang="en">
<head>
<meta charset="utf-8">
<title>Quillbrook Networks Ltd. — Business Cards</title>
<link href="https://fonts.googleapis.com/css2?family=Montserrat:wght@500;600&family=Roboto:ital,wght@0,400;0,500;1,400&display=swap" rel="stylesheet">
<style>
  :root {
    --backdrop: #aaa8a8;
    --card-dark: #1f1f1f;
    --card-dark-pattern: #262626;
    --card-light: #f1f1f1;
    --brand-blue: #1d8fd8;
    --text-dark: #3a3a3a;
    --text-muted: #555555;
    --text-on-dark: #e6e6e6;
  }
  * { margin: 0; padding: 0; box-sizing: border-box; }
  html, body {
    width: 1200px; height: 1200px; overflow: hidden;
    background: var(--backdrop);
  }
  .canvas { position: relative; width: 1200px; height: 1200px; }

  .card { position: absolute; }
  .card--front {
    left: 238px; top: 117px; width: 714px; height: 420px;
    background: var(--card-dark);
  }
  .card--back {
    left: 230px; top: 644px; width: 727px; height: 417px;
    background: var(--card-light);
  }

  .card__pattern {
    position: absolute; inset: 0;
    background: linear-gradient(135deg, var(--card-dark-pattern), var(--card-dark));
  }

  .brand-name {
    position: absolute; left: 0; right: 0; text-align: center;
    font-family: "Montserrat", sans-serif;
    font-weight: 600;
    font-size: 44px;
    color: var(--brand-blue);
    letter-spacing: 0.2px;
  }
  .card--front .brand-name { top: 188px; }
  .card--back .brand-name { top: 80px; }

  .tagline {
    position: absolute; left: 0; right: 0;
    display: flex; align-items: center; justify-content: center; gap: 18px;
    font-family: "Montserrat", sans-serif; font-weight: 500;
    font-size: 18px;
  }
  .tagline__rule {
    width: 108px; height: 3px; background: var(--brand-blue);
    border-radius: 2px;
  }
  .card--front .tagline { top: 377px; color: var(--text-on-dark); }
  .card--back .tagline { top: 364px; color: var(--text-dark); }

  .person {
    position: absolute; left: 140px; top: 238px; width: 168px; text-align: right;
    font-family: "Roboto", sans-serif;
  }
  .person__name {
    font-weight: 500; font-size: 25px; color: var(--brand-blue);
    font-family: "Montserrat", sans-serif; font-weight: 600;
  }
  .person__title {
    margin-top: 4px; font-style: italic; font-size: 16px; color: var(--text-muted);
  }

  .contact-list {
    position: absolute; left: 334px; top: 229px; list-style: none;
    font-family: "Roboto", sans-serif; font-size: 18px; color: var(--text-dark);
  }
  .contact-list li {
    display: flex; align-items: center; gap: 16px; height: 27px;
  }
  .contact-list svg { width: 19px; height: 16px; fill: var(--brand-blue); }
</style>
</head>
<body>
<main class="canvas">

  <section class="card card--front">
    <div class="card__pattern" role="img" aria-label="Subtle dark background pattern of repeating outlined shapes"></div>
    <div class="brand-name">Quillbrook Networks Ltd.</div>
    <div class="tagline">
      <span class="tagline__rule"></span>
      <span>Revolutionizing IT Services</span>
      <span class="tagline__rule"></span>
    </div>
  </section>

  <section class="card card--back">
    <div class="brand-name">Quillbrook Networks Ltd.</div>

    <div class="person">
      <div class="person__name">Daniel Reyes</div>
      <div class="person__title">Managing Director</div>
    </div>

    <ul class="contact-list">
      <li>
        <svg viewBox="0 0 20 16" aria-hidden="true">
          <path d="M2 5c0-2 3-3 8-3s8 1 8 3v1.5h-4V5c-1-.6-2.5-.8-4-.8S7 4.4 6 5v1.5H2z"/>
          <path d="M4 8h12l2 6.5H2z"/>
        </svg>
        <span>604-555-0148</span>
      </li>
      <li>
        <svg viewBox="0 0 16 16" aria-hidden="true">
          <path d="M8 1a7 7 0 1 0 0 14A7 7 0 0 0 8 1zm0 1.3c.9 0 1.8 1.6 2.1 4H5.9C6.2 3.9 7.1 2.3 8 2.3zM2.4 7.3h2.2a12 12 0 0 0 0 1.4H2.4a5.7 5.7 0 0 1 0-1.4zm3.5 0h4.2a12 12 0 0 1 0 1.4H5.9a12 12 0 0 1 0-1.4zm5.5 0h2.2a5.7 5.7 0 0 1 0 1.4h-2.2a12 12 0 0 0 0-1.4zM5.9 9.7h4.2c-.3 2.4-1.2 4-2.1 4s-1.8-1.6-2.1-4z"/>
        </svg>
        <span>www.quillbrook.me</span>
      </li>
      <li>
        <svg viewBox="0 0 18 14" aria-hidden="true">
          <path d="M0 1h18v12H0zm2 1.5L9 8l7-5.5v-.1H2zm-.6 9.1h15.2L11 6.7 9 8.3 7 6.7z"/>
        </svg>
        <span>support@quillbrook.me</span>
      </li>
    </ul>

    <div class="tagline">
      <span class="tagline__rule"></span>
      <span>Revolutionizing IT Services</span>
      <span class="tagline__rule"></span>
    </div>
  </section>

</main>
</body>
</html>
```